Corvane Card

The logo is the Spanish flag colors I want a vibrant eye catching design with the yellow / red colors over either Navy or white background or black even ,
Would like a 2D feel to the logo with another lighter color logo under it look ,

Contact Information for Business Card

Corvane Flooring
Teodor Vashkin
Main Number
Cell Number
Fax Number

Website on the side of the card somewhere

Font styles to use
Sans Serif

Colors
ec1f27
ffc214

Requirements
Must have
• 2 logos feel one is bolder and the other one underneath very light

```html
<!DOCTYPE html>
<html lang="en">
<head>
<meta charset="utf-8">
<title>Corvane Card</title>
<link rel="stylesheet" href="https://fonts.googleapis.com/css2?family=Open+Sans:wght@400;600;700&display=swap">
<style>
  :root {
    --red: #ec1f27;
    --yellow: #ffc214;
    --gold: #e4b02a;
    --navy: #12174a;
    --ink: #1d1d1d;
    --paper: #ffffff;
    --backdrop: #e9e7e4;
  }
  * { box-sizing: border-box; margin: 0; padding: 0; }
  html, body {
    width: 1200px; height: 997px; overflow: hidden;
    background: var(--backdrop);
    font-family: "Open Sans", sans-serif;
  }
  .sheet {
    width: 1200px; height: 997px;
    display: flex; flex-direction: column; align-items: center; justify-content: center;
    gap: 56px;
  }
  .card {
    position: relative; width: 700px; height: 400px; overflow: hidden;
    box-shadow: 0 6px 20px rgba(0,0,0,.12);
  }
  /* Front */
  .card--front { background: var(--paper); }
  .swoosh { position: absolute; inset: 0; }
  .holder { position: absolute; top: 40px; right: 44px; text-align: right; }
  .holder__name { color: var(--red); font-weight: 700; font-size: 24px; letter-spacing: .5px; line-height: 1.1; }
  .holder__role { color: var(--ink); font-size: 14px; margin-top: 3px; }
  .address { position: absolute; top: 118px; right: 44px; text-align: right; font-size: 15px; line-height: 1.3; color: var(--ink); }
  .address__company { color: var(--gold); font-weight: 600; }
  .brand { position: absolute; left: 48px; top: 170px; display: flex; align-items: center; gap: 12px; }
  .brand__square { width: 30px; height: 30px; background: var(--red); }
  .brand__name { color: var(--gold); font-weight: 700; font-size: 30px; letter-spacing: 1px; }
  .contacts { position: absolute; left: 48px; bottom: 62px; list-style: none; font-size: 15px; color: var(--ink); }
  .contacts li { display: flex; align-items: center; gap: 10px; line-height: 1.55; }
  .contacts svg { width: 16px; height: 16px; flex: none; }
  /* Back */
  .card--back { background: var(--navy); display: flex; flex-direction: column; align-items: center; justify-content: center; }
  .back-brand { display: flex; align-items: center; gap: 14px; }
  .back-brand__square { width: 36px; height: 36px; background: var(--red); }
  .back-brand__name { color: var(--yellow); font-weight: 700; font-size: 38px; letter-spacing: 1.5px; }
  .website { margin-top: 46px; font-size: 17px; letter-spacing: 3px; color: var(--yellow); }
  .website__prefix { color: var(--red); }
</style>
</head>
<body>
<main class="sheet">
  <section class="card card--front" aria-label="Business card front">
    <svg class="swoosh" viewBox="0 0 700 400" aria-hidden="true">
      <path d="M0 400 C260 395 470 290 700 200 L700 250 C480 320 260 400 120 400Z" fill="var(--red)"/>
      <path d="M0 400 C250 398 480 320 700 256 L700 266 C480 332 260 400 0 400Z" fill="var(--gold)"/>
    </svg>
    <div class="holder">
      <p class="holder__name">TEODOR VASHKIN</p>
      <p class="holder__role">Managing Director</p>
    </div>
    <div class="address">
      <p class="address__company">Corvane Flooring</p>
      <p>Suite 102 Street name, State,</p>
      <p>Zip 2034, Country</p>
    </div>
    <div class="brand">
      <span class="brand__square"></span>
      <span class="brand__name">CORVANE FLOORING</span>
    </div>
    <ul class="contacts">
      <li>
        <svg viewBox="0 0 16 16" aria-hidden="true"><rect width="16" height="16" fill="var(--red)"/><path d="M5 3.5h2l1 2.5-1.3.9a6 6 0 0 0 2.4 2.4l.9-1.3 2.5 1v2c0 .6-.5 1-1 1A8 8 0 0 1 4 4.5c0-.5.4-1 1-1z" fill="#fff"/></svg>
        0140 555 019
      </li>
      <li>
        <svg viewBox="0 0 16 16" aria-hidden="true"><rect width="16" height="16" fill="var(--red)"/><rect x="5" y="3" width="6" height="3" fill="#fff"/><rect x="3" y="7" width="10" height="4" fill="#fff"/><rect x="5" y="10" width="6" height="3" fill="#fff" stroke="var(--red)" stroke-width=".8"/></svg>
        3333 555 018
      </li>
      <li>
        <svg viewBox="0 0 16 16" aria-hidden="true"><rect width="16" height="16" fill="var(--red)"/><rect x="3" y="4.5" width="10" height="7" fill="#fff"/><path d="M3 4.5l5 4 5-4" fill="none" stroke="var(--red)" stroke-width="1"/></svg>
        info@corvaneflooring.com
      </li>
    </ul>
  </section>

  <section class="card card--back" aria-label="Business card back">
    <div class="back-brand">
      <span class="back-brand__square"></span>
      <span class="back-brand__name">CORVANE FLOORING</span>
    </div>
    <p class="website"><span class="website__prefix">www.</span>corvaneflooring.com</p>
  </section>
</main>
</body>
</html>
```